Lumbrix Design

Looking for Lumbrix banner and square design:
Lumbrix Banner
W:1600 px H:400 px
Square
120x120

Logo attached.

Description: Data-Driven stock market portfolio management using quantitative analysis.

```html
<!DOCTYPE html>
<html lang="en">
<head>
<meta charset="utf-8">
<title>Lumbrix Banner and Square</title>
<link rel="stylesheet" href="https://fonts.googleapis.com/css2?family=Montserrat:ital,wght@0,300;0,500;0,600;0,800;1,300&display=swap">
<style>
  :root {
    --page: #f2f3f5;
    --banner-light: #f7f7f8;
    --banner-tint: #e3eef8;
    --brand-blue: #0a72bd;
    --brand-blue-bright: #0b8ee6;
    --brand-navy: #16375f;
    --square-deep: #1d5f92;
    --white: #ffffff;
    --art-light: #d4e4f4;
    --art-mid: #8fb7e0;
  }
  * { margin: 0; padding: 0; box-sizing: border-box; }
  html, body {
    width: 1200px;
    height: 568px;
    overflow: hidden;
    background: var(--page);
    font-family: "Montserrat", sans-serif;
  }
  .canvas { position: relative; width: 1200px; height: 568px; }

  .banner {
    position: absolute;
    left: 62px;
    top: 139px;
    width: 1076px;
    height: 269px;
    overflow: hidden;
    background: linear-gradient(100deg, var(--banner-light) 0%, var(--banner-light) 52%, var(--banner-tint) 100%);
  }
  .banner__wedge { position: absolute; left: 0; top: 0; }

  .banner__headline {
    position: absolute;
    left: 60px;
    top: 62px;
    font-weight: 800;
    font-size: 52px;
    letter-spacing: 1px;
    color: var(--brand-blue);
    line-height: 1;
  }
  .banner__subtitle {
    position: absolute;
    left: 60px;
    top: 117px;
    font-weight: 300;
    font-style: italic;
    font-size: 25px;
    line-height: 28px;
    color: var(--brand-navy);
    text-transform: uppercase;
  }
  .banner__tag {
    position: absolute;
    left: 60px;
    top: 183px;
    width: 230px;
    height: 22px;
    background: var(--brand-blue);
    color: var(--white);
    font-weight: 600;
    font-size: 13.5px;
    line-height: 22px;
    text-align: center;
    letter-spacing: 0.2px;
  }
  .banner__art {
    position: absolute;
    left: 560px;
    top: 21px;
    width: 311px;
    height: 226px;
    border-radius: 14px;
    background: radial-gradient(ellipse at 55% 50%, var(--art-mid) 0%, var(--art-light) 60%, rgba(212,228,244,0) 100%);
  }
  .banner__brand {
    position: absolute;
    left: 898px;
    top: 32px;
    display: flex;
    align-items: center;
    gap: 8px;
  }
  .banner__brand-dot {
    width: 22px;
    height: 22px;
    border-radius: 50%;
    background: var(--brand-blue);
  }
  .banner__brand-name {
    font-weight: 500;
    font-size: 22px;
    color: var(--brand-blue);
    letter-spacing: 0.5px;
  }

  .square {
    position: absolute;
    left: 568px;
    top: 367px;
    width: 85px;
    height: 85px;
    border: 3px solid var(--white);
    background: linear-gradient(135deg, var(--brand-blue) 0%, var(--square-deep) 100%);
    display: flex;
    align-items: center;
    justify-content: center;
  }
  .square__name {
    font-weight: 600;
    font-size: 16px;
    color: var(--white);
  }
</style>
</head>
<body>
<div class="canvas">
  <section class="banner">
    <svg class="banner__wedge" width="1076" height="269" viewBox="0 0 1076 269" aria-hidden="true">
      <defs>
        <linearGradient id="wedgeFill" x1="0" y1="0" x2="1" y2="0">
          <stop offset="0" stop-color="#0b8ee6"/>
          <stop offset="1" stop-color="#0a72bd"/>
        </linearGradient>
      </defs>
      <polygon points="338,269 790,173 1076,269" fill="url(#wedgeFill)"/>
    </svg>

    <h1 class="banner__headline">DATA-DRIVEN</h1>
    <p class="banner__subtitle">Stock Market Portfolio<br>Management</p>
    <p class="banner__tag">USING QUANTITATIVE ANALYSIS</p>

    <div class="banner__art" role="img" aria-label="Isometric illustration of a financial dashboard platform with charts, coins and people analysing data"></div>

    <div class="banner__brand">
      <span class="banner__brand-dot"></span>
      <span class="banner__brand-name">Lumbrix</span>
    </div>
  </section>

  <div class="square">
    <span class="square__name">Lumbrix</span>
  </div>
</div>
</body>
</html>
```